We want to design total new business card and logo for Kestrel Building Services Ltd

Our company name Kestrel Building Services Ltd. Design new logo and business card , need hi-end luxury style art for architecture and construction industry. The card should simple but stylish. Our business focus on CONNECT tradesman to construction company, help marketing construction company tender oversea projects, managing franchise in construction sector, delivery amazing services to our client, so Logo should show the CONNECTION IDEA, CONNECTING PEOPLE, LUXURY. Visit our website for more information: kestrelgroup.example.nz

Target Market(s)

Directors or managers

Industry/Entity Type

Construction Company

Contact Information for Business Card

Name, Title, Mobile, Email, Website

Font styles to use
Serif

Colors

Designer to choose colors to be used in the design.

Requirements
Must have
• Simple and luxury, connection icon
Nice to have
• Special materials, plastic card, look through,...
• Look new ideas.

```html
<!DOCTYPE html>
<html lang="en">
<head>
<meta charset="utf-8">
<title>Kestrel Building Services Ltd – Business Card</title>
<link rel="stylesheet" href="https://fonts.googleapis.com/css2?family=Source+Sans+3:wght@400;600&display=swap">
<style>
  :root {
    --page: #d9dadb;
    --card-light: #f1f2f2;
    --card-mist: #e2e4e5;
    --navy: #1b3c80;
    --navy-deep: #0f2862;
    --brand-blue: #1f4a9c;
    --ink: #3f4248;
    --on-navy: #f2f5fb;
    --accent: #4aa9dc;
  }
  * { margin: 0; padding: 0; box-sizing: border-box; }
  html, body { width: 1200px; height: 971px; overflow: hidden; }
  body {
    background: var(--page);
    font-family: "Source Sans 3", "Segoe UI", sans-serif;
    position: relative;
  }
  .card {
    position: absolute;
    left: 120px; top: 205px;
    width: 960px; height: 560px;
    border-radius: 24px;
    overflow: hidden;
    background: linear-gradient(135deg, var(--card-light), var(--card-mist));
    box-shadow: 0 10px 30px rgba(0,0,0,.15);
  }
  .card__panel {
    position: absolute; inset: 0;
    background: linear-gradient(160deg, var(--navy) 0%, var(--navy-deep) 100%);
    clip-path: polygon(57% 0, 100% 0, 100% 100%, 35% 100%);
  }
  .brand {
    position: absolute;
    left: 90px; top: 150px;
    display: flex; align-items: center; gap: 18px;
  }
  .brand__mark {
    width: 26px; height: 26px;
    background: var(--brand-blue);
  }
  .brand__name {
    color: var(--brand-blue);
    font-weight: 600;
    font-size: 40px;
    line-height: 1.1;
    letter-spacing: .5px;
  }
  .person {
    position: absolute;
    left: 0; top: 400px;
    display: flex; align-items: center; gap: 26px;
  }
  .person__tab {
    width: 30px; height: 66px;
    background: var(--navy-deep);
    border-radius: 0 8px 8px 0;
  }
  .person__name {
    color: var(--navy);
    font-weight: 600;
    font-size: 34px;
    line-height: 1.1;
  }
  .person__title {
    color: var(--ink);
    font-size: 24px;
    line-height: 1.3;
  }
  .contact {
    position: absolute;
    right: 60px; top: 280px;
    color: var(--on-navy);
    font-size: 24px;
    text-align: right;
    line-height: 1.35;
  }
  .contact__address { margin-bottom: 24px; }
  .contact__line {
    display: flex; justify-content: flex-end; align-items: center; gap: 10px;
  }
  .contact__icon { width: 22px; height: 22px; flex: none; }
</style>
</head>
<body>
  <div class="card">
    <div class="card__panel"></div>

    <div class="brand">
      <div class="brand__mark"></div>
      <div class="brand__name">Kestrel Building<br>Services Ltd</div>
    </div>

    <div class="person">
      <div class="person__tab"></div>
      <div>
        <div class="person__name">Daniel Whitford</div>
        <div class="person__title">Managing Director</div>
      </div>
    </div>

    <div class="contact">
      <div class="contact__address">18 Tarata Lane, Riverhead<br>Auckland 0820, New Zealand</div>
      <div class="contact__line">0800 555 0142
        <svg class="contact__icon" viewBox="0 0 24 24"><path fill="var(--accent)" d="M6.6 10.8a15.1 15.1 0 0 0 6.6 6.6l2.2-2.2a1 1 0 0 1 1-.25 11.4 11.4 0 0 0 3.6.57 1 1 0 0 1 1 1V20a1 1 0 0 1-1 1A17 17 0 0 1 3 4a1 1 0 0 1 1-1h3.5a1 1 0 0 1 1 1c0 1.25.2 2.45.57 3.57a1 1 0 0 1-.25 1z"/></svg>
      </div>
      <div class="contact__line">hello@kestrelgroup.example.nz
        <svg class="contact__icon" viewBox="0 0 24 24" fill="none" stroke="var(--accent)" stroke-width="1.8"><rect x="3" y="5" width="18" height="14" rx="1"/><path d="M3 6l9 7 9-7"/></svg>
      </div>
      <div class="contact__line">www.kestrelgroup.example.nz
        <svg class="contact__icon" viewBox="0 0 24 24" fill="none" stroke="var(--accent)" stroke-width="1.6"><circle cx="12" cy="12" r="9"/><ellipse cx="12" cy="12" rx="4" ry="9"/><path d="M3 12h18M5 7h14M5 17h14"/></svg>
      </div>
    </div>
  </div>
</body>
</html>
```